Upmarket Dessert Lounge needs a Business Card Design

We are an upmarket dessert lounge needing a business card to match our image.

We want something that is simple yet beautiful, feminine, classy, sophisticated and elegant. We want it to stand out and don't mind if it is bold.

The design should include our logo and colours of red or maroon with gold highlights. We don't mind if black is used.

Marlow & Quince

Target Market(s)

For those who like to indulge or treat themselves and give in to their temptations on good quality desserts.

Industry/Entity Type

Business

Requirements
Must have
• Must include our logo and our name

Marlow & Quince

M & Q

```html
<!DOCTYPE html>
<html lang="en">
<head>
<meta charset="utf-8">
<title>Marlow &amp; Quince — Business Card</title>
<link rel="stylesheet" href="https://fonts.googleapis.com/css2?family=Lora:wght@400;700&family=Open+Sans:wght@400;600&display=swap">
<style>
  :root {
    --page: #e9e6e2;
    --red-light: #a82622;
    --red: #861a17;
    --red-deep: #560b0a;
    --gold: #e0b07a;
    --ink: #1f1a18;
    --white: #ffffff;
    --serif: "Lora", Georgia, serif;
    --sans: "Open Sans", Arial, sans-serif;
  }
  * { box-sizing: border-box; margin: 0; padding: 0; }
  html, body { width: 1200px; height: 951px; overflow: hidden; }
  body { background: var(--page); position: relative; }

  .card {
    position: absolute;
    width: 600px;
    height: 343px;
    border-radius: 22px;
    overflow: hidden;
    box-shadow: 0 10px 28px rgba(0,0,0,.28);
  }

  /* Brand mark: name in text font with one plain circle beside it */
  .brand-mark {
    position: absolute;
    display: flex;
    align-items: center;
    font-family: var(--serif);
    font-weight: 400;
    text-transform: uppercase;
    color: var(--gold);
    white-space: nowrap;
  }
  .brand-dot {
    flex: none;
    border-radius: 50%;
    background: var(--gold);
  }

  /* Front */
  .card-front {
    left: 90px; top: 90px;
    background: radial-gradient(ellipse at 45% 45%, var(--red-light) 0%, var(--red) 45%, var(--red-deep) 100%);
  }
  .front-flourish {
    position: absolute;
    right: 20px; top: 4px;
    width: 260px; height: 70px;
    border-radius: 35px;
    background: radial-gradient(ellipse at center, rgba(224,176,122,.55) 0%, rgba(224,176,122,.15) 60%, rgba(224,176,122,0) 100%);
  }
  .front-mark {
    left: 0; right: 0; top: 140px;
    justify-content: center;
    gap: 14px;
    font-size: 36px;
    letter-spacing: 2px;
  }
  .front-mark .brand-dot { width: 16px; height: 16px; }
  .front-web {
    position: absolute;
    left: 0; right: 0; bottom: 50px;
    text-align: center;
    font-family: var(--serif);
    font-weight: 700;
    font-size: 17px;
    letter-spacing: .5px;
    color: var(--white);
  }

  /* Back */
  .card-back {
    left: 510px; top: 518px;
    background: var(--ink);
  }
  .back-bands { position: absolute; inset: 0; }
  .back-mark {
    left: 118px; top: 58px;
    gap: 8px;
    font-size: 19px;
    letter-spacing: 1px;
  }
  .back-mark .brand-dot { width: 9px; height: 9px; }
  .back-title {
    position: absolute;
    right: 34px; top: 96px;
    font-family: var(--sans);
    font-weight: 600;
    font-size: 19px;
    color: var(--gold);
  }
  .back-title .amp { color: var(--white); }
  .contact-list, .address {
    position: absolute;
    list-style: none;
    font-family: var(--sans);
    font-size: 16px;
    line-height: 22px;
    color: var(--white);
  }
  .contact-list { left: 30px; top: 196px; }
  .contact-list li { display: flex; align-items: center; gap: 8px; }
  .contact-list svg { width: 14px; height: 14px; flex: none; }
  .address { left: 330px; top: 230px; display: flex; gap: 8px; }
  .address svg { width: 14px; height: 14px; margin-top: 4px; flex: none; }
  .address address { font-style: normal; }
</style>
</head>
<body>

<section class="card card-front" aria-label="Card front">
  <div class="front-flourish" role="img" aria-label="Gold floral flourish ornament"></div>
  <h1 class="brand-mark front-mark"><span class="brand-dot"></span>Marlow &amp; Quince</h1>
  <p class="front-web">www.marlowquince.com</p>
</section>

<section class="card card-back" aria-label="Card back">
  <svg class="back-bands" viewBox="0 0 600 343" preserveAspectRatio="none" aria-hidden="true">
    <path d="M0 0 H150 C90 20 30 70 0 120 Z" fill="var(--gold)"/>
    <path d="M0 0 H120 C70 20 25 60 0 100 Z" fill="var(--red)"/>
    <path d="M600 140 V343 H400 C500 320 570 240 600 140 Z" fill="var(--gold)"/>
    <path d="M600 175 V343 H440 C530 320 585 260 600 175 Z" fill="var(--red)"/>
  </svg>

  <p class="brand-mark back-mark"><span class="brand-dot"></span>Marlow &amp; Quince</p>
  <p class="back-title">Marlow <span class="amp">&amp;</span> Quince</p>

  <ul class="contact-list">
    <li>
      <svg viewBox="0 0 16 16"><path d="M4 1 L6.5 4 L5 6 C6 8.5 7.5 10 10 11 L12 9.5 L15 12 L13 15 C7 15 1 9 1 3 Z" fill="var(--gold)"/></svg>
      555-014-2200
    </li>
    <li>
      <svg viewBox="0 0 16 16"><rect x="2" y="6" width="12" height="8" rx="1" fill="var(--gold)"/><rect x="4" y="1" width="8" height="5" fill="var(--gold)"/></svg>
      555-014-2201
    </li>
    <li>
      <svg viewBox="0 0 16 16"><rect x="1" y="3" width="14" height="10" rx="1" fill="var(--gold)"/><path d="M1 4 L8 9 L15 4" stroke="var(--ink)" stroke-width="1.4" fill="none"/></svg>
      info@marlowquince.com
    </li>
    <li>
      <svg viewBox="0 0 16 16"><circle cx="8" cy="8" r="7" fill="var(--gold)"/></svg>
      www.marlowquince.com
    </li>
  </ul>

  <div class="address">
    <svg viewBox="0 0 16 16"><path d="M8 1 L15 8 H13 V15 H9.5 V10.5 H6.5 V15 H3 V8 H1 Z" fill="var(--gold)"/></svg>
    <address>1480 Alder Crest Rd.<br>Suite 204-118<br>Halden, TX 75019</address>
  </div>
</section>

</body>
</html>
```